Create a new business card

I’m looking to update my business card to make it match the rest of my brand. I will include my current website as well as what my vehicle designs look like, etc..
What my business currently services
Weekly maintenance pool openings / closings
Equipment repair, including pumps, heaters, salt systems, filters, etc.
We install automatic covers and maintain them as well as provide preventative maintenance

I would like to include my name.
Dorian Pelkin.
My title
Owner
My email
Dorian@tidewellnx.com
4015827160
Www.tidewellnx.com

```html
<!DOCTYPE html>
<html lang="en">
<head>
<meta charset="utf-8">
<title>Tidewell Pool Service – Business Card</title>
<link href="https://fonts.googleapis.com/css2?family=Montserrat:wght@400;500;600;700;800&display=swap" rel="stylesheet">
<style>
  :root {
    --bg: #e9ecef;
    --navy: #1f2a66;
    --sky: #3aa9e6;
    --sky-light: #8fdcff;
    --water-deep: #1d8fc9;
    --water-mid: #39a9df;
    --water-light: #7fd0f2;
    --white: #ffffff;
  }
  * { box-sizing: border-box; margin: 0; padding: 0; }
  html, body { width: 1200px; height: 900px; overflow: hidden; }
  body {
    background: var(--bg);
    font-family: "Montserrat", sans-serif;
    position: relative;
  }
  .card {
    position: absolute;
    left: 250px;
    width: 700px;
    height: 400px;
    border-radius: 22px;
    overflow: hidden;
    box-shadow: 0 10px 30px rgba(20, 30, 60, 0.18);
  }
  .card--services { top: 40px; }
  .card--contact { top: 470px; background: var(--white); }

  .water {
    position: absolute; inset: 0;
    background:
      radial-gradient(ellipse at 30% 40%, var(--water-light) 0%, transparent 55%),
      linear-gradient(135deg, var(--water-mid) 0%, var(--water-deep) 100%);
  }
  .brand {
    position: absolute;
    display: flex;
    align-items: center;
    gap: 12px;
    font-weight: 700;
    font-size: 26px;
    line-height: 1.15;
  }
  .brand__dot {
    width: 22px; height: 22px; border-radius: 50%;
    flex: none;
  }
  .card--services .brand { left: 60px; top: 160px; color: var(--white); }
  .card--services .brand__dot { background: var(--white); }
  .card--contact .brand { left: 60px; top: 160px; color: var(--navy); }
  .card--contact .brand__dot { background: var(--sky); }

  .divider {
    position: absolute;
    left: 340px;
    top: 70px;
    width: 2px;
    height: 260px;
  }
  .card--services .divider { background: rgba(255,255,255,0.6); }
  .card--contact .divider { background: var(--navy); top: 60px; height: 160px; }

  .services {
    position: absolute;
    left: 375px;
    top: 80px;
    color: var(--white);
  }
  .services__title {
    font-weight: 700;
    font-size: 26px;
    color: var(--sky-light);
    letter-spacing: 0.5px;
    margin-bottom: 12px;
  }
  .services__list { list-style: none; font-size: 16px; font-weight: 500; }
  .services__list li { margin-bottom: 7px; white-space: nowrap; }
  .services__list li::before { content: "• "; }

  .contact {
    position: absolute;
    left: 375px;
    top: 62px;
    color: var(--navy);
  }
  .contact__name { font-weight: 800; font-size: 30px; }
  .contact__role { font-size: 17px; font-weight: 500; margin-bottom: 18px; }
  .contact__list { list-style: none; font-size: 16px; font-weight: 500; }
  .contact__list li { display: flex; align-items: center; gap: 10px; margin-bottom: 6px; }
  .contact__list svg { width: 15px; height: 15px; fill: var(--sky); flex: none; }

  .swoosh { position: absolute; inset: 0; width: 700px; height: 400px; }
</style>
</head>
<body>

<section class="card card--services">
  <div class="water" role="img" aria-label="Rippling blue pool water background"></div>
  <div class="brand"><span class="brand__dot"></span><span>Tidewell<br>Pool Service</span></div>
  <div class="divider"></div>
  <div class="services">
    <h2 class="services__title">OUR SERVICES</h2>
    <ul class="services__list">
      <li>Weekly pool maintenance</li>
      <li>Pool openings and closings</li>
      <li>Pump, heater &amp; filter repair</li>
      <li>Salt system service</li>
      <li>Automatic cover installation</li>
      <li>Preventative maintenance</li>
    </ul>
  </div>
</section>

<section class="card card--contact">
  <svg class="swoosh" viewBox="0 0 700 400" preserveAspectRatio="none">
    <path d="M700 60 C690 230 560 300 300 340 C230 352 200 370 190 400 L700 400 Z" fill="var(--navy)"/>
    <path d="M676 40 C690 130 650 210 560 250" fill="none" stroke="var(--sky)" stroke-width="7"/>
  </svg>
  <div class="brand"><span class="brand__dot"></span><span>Tidewell<br>Pool Service</span></div>
  <div class="divider"></div>
  <div class="contact">
    <h1 class="contact__name">Dorian Pelkin</h1>
    <p class="contact__role">Owner</p>
    <ul class="contact__list">
      <li><svg viewBox="0 0 24 24"><path d="M6.6 10.8a15.1 15.1 0 0 0 6.6 6.6l2.2-2.2c.3-.3.7-.4 1-.2 1.1.4 2.3.6 3.6.6.6 0 1 .4 1 1V20c0 .6-.4 1-1 1A17 17 0 0 1 3 4c0-.6.4-1 1-1h3.5c.6 0 1 .4 1 1 0 1.3.2 2.5.6 3.6.1.3 0 .7-.2 1z"/></svg>4015827160</li>
      <li><svg viewBox="0 0 24 24"><path d="M2 5h20v14H2z M2 5l10 8 10-8" /></svg>Dorian@tidewellnx.com</li>
      <li><svg viewBox="0 0 24 24"><circle cx="12" cy="12" r="10"/></svg>Www.tidewellnx.com</li>
    </ul>
  </div>
</section>

</body>
</html>
```